Corvane Holdings , new business card design

investment firm with corporate clients . need double sided business card , vertical and horizontal options ,logo must be clear. prefer pantone colors only and sharp design. website also www.corvane.ae

Khalid Bin Tarrafi
Managing Director
Tel. +971 4 387 2940
Mobile +971 50 518 2403
khalid@corvane.ae
Q-Span Plaza, officw 18-B07, Warqa Gardens, Dubai

Contact Information for Business Card

Khalid Bin Tarrafi
Managing Director

Font styles to use
Serif

Colors

Designer to choose colors to be used in the design.

```html
<!DOCTYPE html>
<html lang="en">
<head>
<meta charset="utf-8">
<title>Corvane Holdings – Business Card</title>
<link href="https://fonts.googleapis.com/css2?family=Mulish:wght@300;400;700&display=swap" rel="stylesheet">
<style>
  :root {
    --bg: #e8e6e4;
    --card-white: #fbfbfb;
    --brand-blue: #4a7199;
    --band-shadow: #cfcac6;
    --text-dark: #3c3c3c;
    --text-grey: #555a60;
    --divider: #b9c4cf;
    --white: #ffffff;
  }
  * { margin: 0; padding: 0; box-sizing: border-box; }
  html, body {
    width: 1200px; height: 997px; overflow: hidden;
    background: var(--bg);
    font-family: "Mulish", sans-serif;
  }
  .stage {
    position: relative; width: 1200px; height: 997px;
    display: flex; align-items: center; justify-content: center; gap: 60px;
  }
  .card {
    position: relative; width: 500px; height: 286px;
    box-shadow: 0 2px 6px rgba(0,0,0,0.12);
    overflow: hidden;
  }
  /* front */
  .card--front { background: var(--card-white); }
  .front-band {
    position: absolute; left: 0; top: 0; bottom: 0; width: 46px;
    background: var(--brand-blue);
    border-right: 8px solid var(--band-shadow);
  }
  .wordmark {
    font-weight: 300; letter-spacing: 0.32em; text-transform: uppercase;
    white-space: nowrap; line-height: 1;
  }
  .front-wordmark {
    position: absolute; right: 28px; top: 34px;
    font-size: 20px; color: var(--text-dark);
  }
  .contact-block { position: absolute; left: 84px; top: 150px; }
  .person-name { font-size: 17px; font-weight: 700; color: var(--brand-blue); }
  .person-title { font-size: 13px; color: var(--text-grey); margin-top: 2px; }
  .contact-list {
    list-style: none; margin-top: 12px;
  }
  .contact-list li {
    display: flex; align-items: center;
    font-size: 12.5px; color: var(--text-grey); height: 19px;
  }
  .contact-icon {
    width: 12px; height: 12px; margin-right: 9px; flex: none;
    fill: var(--brand-blue);
  }
  .contact-text {
    border-left: 1px solid var(--divider); padding-left: 8px; line-height: 19px;
  }
  /* back */
  .card--back {
    background: var(--brand-blue);
    display: flex; align-items: center; justify-content: center;
  }
  .back-wordmark { font-size: 26px; color: var(--white); }
</style>
</head>
<body>
<main class="stage">
  <section class="card card--front" aria-label="Business card front">
    <div class="front-band"></div>
    <div class="wordmark front-wordmark">Corvane Holdings</div>
    <div class="contact-block">
      <p class="person-name">Khalid Bin Tarrafi</p>
      <p class="person-title">Managing Director</p>
      <ul class="contact-list">
        <li>
          <svg class="contact-icon" viewBox="0 0 24 24" aria-hidden="true"><path d="M6.6 10.8a15.1 15.1 0 0 0 6.6 6.6l2.2-2.2a1 1 0 0 1 1-.25 11.4 11.4 0 0 0 3.6.57 1 1 0 0 1 1 1V20a1 1 0 0 1-1 1A17 17 0 0 1 3 4a1 1 0 0 1 1-1h3.5a1 1 0 0 1 1 1c0 1.25.2 2.45.57 3.57a1 1 0 0 1-.25 1z"/></svg>
          <span class="contact-text">+971 4 387 2940</span>
        </li>
        <li>
          <svg class="contact-icon" viewBox="0 0 24 24" aria-hidden="true"><path d="M7 1h10a2 2 0 0 1 2 2v18a2 2 0 0 1-2 2H7a2 2 0 0 1-2-2V3a2 2 0 0 1 2-2zm0 3v14h10V4zm5 15.5a1 1 0 1 0 0 2 1 1 0 0 0 0-2z"/></svg>
          <span class="contact-text">+971 50 518 2403</span>
        </li>
        <li>
          <svg class="contact-icon" viewBox="0 0 24 24" aria-hidden="true"><path d="M2 5h20v14H2zm2 2v.5l8 5 8-5V7zm0 2.9V17h16V9.9l-8 5z"/></svg>
          <span class="contact-text">khalid@corvane.ae</span>
        </li>
        <li>
          <svg class="contact-icon" viewBox="0 0 24 24" aria-hidden="true"><path d="M12 2a7 7 0 0 0-7 7c0 5.2 7 13 7 13s7-7.8 7-13a7 7 0 0 0-7-7zm0 9.5A2.5 2.5 0 1 1 12 6.5a2.5 2.5 0 0 1 0 5z"/></svg>
          <span class="contact-text">Q-Span Plaza, officw 18-B07, Warqa Gardens, Dubai</span>
        </li>
      </ul>
    </div>
  </section>

  <section class="card card--back" aria-label="Business card back">
    <div class="wordmark back-wordmark">Corvane Holdings</div>
  </section>
</main>
</body>
</html>
```